Ad-Services Website

The project is for an agency which provides a 360 service around the world of printing and advertising. Without much focus on the advertising per say, but much more focus on the medium on which advertisement can be achieved, such as banners, moving banners, boards and so on.

Futhermore more the company deals with material printing so it has advertising agencies as clients.

Finally it represents several companies in Greece for materials around advertising such as stands, ad-walls, banners and so on.

The webpage needs to have web 2.0 look an feel, and it will lack in content, therefore the focus should not be in large sections of text.

I can have a pdf sent with a small presentation that was done to the client, and the structure to which he agreed to

The following website has the look & feel of what we are looking for

http://www.lumtaro.gr

The companies current website where you can get the colors and logos from is

http://korvibelt.gr
Updates

Hello,

Thank you all very much for your designs, we really appreciate your contribution.

Maybe in our next project we can work together.

Best Regards,
Manos

Industry/Entity Type

Advertising

```html
<!DOCTYPE html>
<html lang="en">
<head>
<meta charset="utf-8">
<title>Nexora Advertising</title>
<link rel="stylesheet" href="https://fonts.googleapis.com/css2?family=Arimo:wght@400&display=swap">
<style>
  :root {
    --brand-teal: #16607f;
    --top-rule: #1a5f7c;
    --ring-stroke: #dddddd;
    --ring-fill: #f7f7f7;
    --bubble-grey: #dcdcdc;
    --placeholder-light: #d6d6d6;
    --placeholder-dark: #b8b8b8;
    --ink: #111111;
    --muted: #9a9a9a;
    --rule: #cfcfcf;
    --page: #ffffff;
    --header-shade: #efefef;
  }
  * { box-sizing: border-box; margin: 0; padding: 0; }
  html, body { width: 1200px; height: 730px; overflow: hidden; background: var(--page); }
  body { font-family: "Arimo", Arial, sans-serif; position: relative; }

  .site-header {
    position: absolute; left: 0; top: 0; width: 1200px; height: 110px;
    border-top: 4px solid var(--top-rule);
    background: linear-gradient(to bottom, var(--header-shade), var(--page));
  }
  .brand {
    position: absolute; left: 178px; top: 38px;
    display: flex; align-items: center; gap: 10px;
    font-size: 34px; line-height: 1; color: var(--ink); letter-spacing: -0.5px;
  }
  .brand-dot {
    width: 14px; height: 14px; border-radius: 50%;
    border: 2px solid var(--brand-teal);
  }

  .services-wheel { position: absolute; left: 0; top: 0; width: 1200px; height: 730px; }
  .hero-illustration {
    position: absolute; left: 420px; top: 276px; width: 294px; height: 182px;
    border-radius: 6px;
    background: linear-gradient(135deg, var(--placeholder-light), var(--placeholder-dark));
  }
  .service {
    position: absolute; width: 128px; height: 128px; border-radius: 50%;
    display: flex; align-items: center; justify-content: center;
    font-size: 16px; color: var(--ink); text-decoration: none;
    background: var(--bubble-grey);
  }
  .service--active { background: var(--brand-teal); color: #ffffff; }
  .service--advertising { left: 361px; top: 144px; }
  .service--print { left: 719px; top: 310px; }
  .service--display { left: 413px; top: 507px; }

  .site-footer {
    position: absolute; left: 176px; top: 686px; width: 846px;
    border-top: 2px solid var(--rule);
  }
  .copyright { position: absolute; left: 8px; top: 11px; font-size: 10.5px; color: var(--muted); white-space: nowrap; }
  .social-links { position: absolute; right: 16px; top: 10px; display: flex; gap: 8px; }
  .social-links span { width: 14px; height: 14px; background: #c4c4c4; display: block; }
</style>
</head>
<body>
  <header class="site-header">
    <div class="brand"><span class="brand-name">nexora advertising</span><span class="brand-dot"></span></div>
  </header>

  <main>
    <svg class="services-wheel" width="1200" height="730" viewBox="0 0 1200 730" aria-hidden="true">
      <circle cx="566" cy="366" r="216" fill="var(--ring-fill)" stroke="var(--ring-stroke)" stroke-width="4"/>
    </svg>
    <div class="hero-illustration" role="img" aria-label="Central brand illustration in black"></div>
    <nav>
      <a class="service service--active service--advertising" href="#">ADVERSTING</a>
      <a class="service service--print" href="#">PRINT</a>
      <a class="service service--display" href="#">DISPLAY</a>
    </nav>
  </main>

  <footer class="site-footer">
    <p class="copyright">© Nexora Advertising 2012 All Rights Reserved</p>
    <div class="social-links" aria-label="Social links">
      <span></span><span></span><span></span><span></span><span></span>
    </div>
  </footer>
</body>
</html>
```